Business Card Design Project

I need a business card design for an Organic drive thru coffee kiosk. We will serve organic coffee, teas & smoothies and will serve healthy breakfast food/snacks for people on the go.
I want the card to have 2-3 colors max (earthy colors like browns, greens and so on).
I have attached the logo I want used and would love to play off the theme of "balance."
Include:
Sun-Leaf Coffee
address: 3712 Pelwin Ct. Linwood, OR 27699
phone: 919-555-0143
website: www.sun-leaf.com (website is not up yet but still include it on card)
email: Dorothy@sun-leaf.com
I want one of the following sayings somewhere on the card (the front or back is fine):
"Sip & Snack Bright, on the run!"
"Break the fast with Sun-Leaf"
Maybe on the back list what we offer:
-Organic coffee, espresso & tea
-Blendora smoothies & protein shakes
-Zippy Tonic (100% fresh local fruit and veggies)
-Vital Nibbles
College age to 55
Business

```html
<!DOCTYPE html>
<html lang="en">
<head>
<meta charset="utf-8">
<title>Sun-Leaf Coffee – Business Card</title>
<link href="https://fonts.googleapis.com/css2?family=Delius&family=Cabin:wght@500&display=swap" rel="stylesheet">
<style>
  :root {
    --page-bg: #ece8e1;
    --leaf-light: #93c54e;
    --leaf: #7cb13d;
    --leaf-deep: #6fa332;
    --roast: #3b2418;
    --roast-light: #4d3224;
    --bean: #7a4330;
    --ink-brown: #4a2a1a;
    --tag-brown: #7c3d28;
    --text-green: #9fd04c;
  }
  * { margin: 0; padding: 0; box-sizing: border-box; }
  html, body { width: 1200px; height: 1181px; overflow: hidden; }
  body {
    position: relative;
    background: var(--page-bg);
    font-family: "Delius", "Trebuchet MS", sans-serif;
  }
  .card {
    position: absolute;
    left: 206px;
    width: 787px;
    height: 453px;
    border-radius: 30px;
    overflow: hidden;
  }
  /* Front */
  .card-front {
    top: 102px;
    background: radial-gradient(ellipse at 50% 40%, var(--leaf-light) 0%, var(--leaf) 60%, var(--leaf-deep) 100%);
  }
  .brand {
    position: absolute;
    top: 136px;
    left: 0;
    width: 100%;
    text-align: center;
  }
  .brand-mark {
    display: block;
    width: 74px;
    height: 74px;
    margin: 0 auto 12px;
    border-radius: 50%;
    background: var(--bean);
  }
  .brand-name {
    display: block;
    font-size: 64px;
    line-height: 1;
    color: var(--ink-brown);
  }
  .brand-tagline {
    display: block;
    margin-top: 14px;
    font-family: "Cabin", Arial, sans-serif;
    font-weight: 500;
    font-size: 14px;
    letter-spacing: 3px;
    color: var(--tag-brown);
  }
  /* Back */
  .card-back {
    top: 616px;
    background: var(--leaf);
  }
  .slogan {
    position: absolute;
    left: 0;
    width: 100%;
    text-align: center;
    font-size: 16px;
    color: var(--roast);
    display: flex;
    justify-content: center;
    align-items: center;
    gap: 6px;
  }
  .slogan-top { top: 22px; }
  .slogan-bottom { top: 410px; }
  .slogan .dot {
    width: 18px; height: 18px; border-radius: 50%;
    background: var(--bean);
  }
  .info-band {
    position: absolute;
    top: 68px;
    left: 0;
    width: 100%;
    height: 316px;
    background: radial-gradient(ellipse at 50% 55%, var(--roast-light) 0%, var(--roast) 75%);
  }
  .band-mark {
    position: absolute;
    left: 40px;
    top: 96px;
    width: 92px;
    height: 124px;
    border-radius: 50%;
    background: var(--bean);
  }
  .contact {
    position: absolute;
    right: 428px;
    top: 116px;
    text-align: right;
    color: var(--text-green);
    font-size: 16px;
    line-height: 22px;
    font-style: normal;
  }
  .contact .address { margin-bottom: 2px; }
  .divider {
    position: absolute;
    left: 392px;
    top: 78px;
    width: 2px;
    height: 160px;
    background: var(--text-green);
    border-radius: 1px;
  }
  .services {
    position: absolute;
    left: 424px;
    top: 110px;
    list-style: none;
    color: var(--text-green);
    font-size: 14px;
    line-height: 18.5px;
  }
  .website {
    position: absolute;
    right: 4px;
    top: 92px;
    height: 130px;
    writing-mode: vertical-rl;
    transform: rotate(180deg);
    text-align: center;
    color: var(--text-green);
    font-size: 13px;
  }
</style>
</head>
<body>
  <section class="card card-front" aria-label="Card front">
    <div class="brand">
      <span class="brand-mark" aria-hidden="true"></span>
      <span class="brand-name">Sun-Leaf</span>
      <span class="brand-tagline">ORGANIC COFFEE + CAFE</span>
    </div>
  </section>

  <section class="card card-back" aria-label="Card back">
    <p class="slogan slogan-top"><span class="dot" aria-hidden="true"></span>Break the fast with Sun-Leaf<span class="dot" aria-hidden="true"></span></p>

    <div class="info-band">
      <span class="band-mark" aria-hidden="true"></span>
      <address class="contact">
        <div class="address">3712 Pelwin Ct. Linwood,<br>OR 27699</div>
        <div>541-555-0143</div>
        <div>Dorothy@sun-leaf.com</div>
      </address>
      <span class="divider" aria-hidden="true"></span>
      <ul class="services">
        <li>Services we offer :</li>
        <li>- Organic coffee, espresso &amp; tea</li>
        <li>- Blendora smoothies &amp; protein shakes</li>
        <li>- Zippy Tonic (100% fresh local fruit and veggies)</li>
        <li>- Vital Nibbles</li>
      </ul>
      <span class="website">www.sun-leaf.com</span>
    </div>

    <p class="slogan slogan-bottom"><span class="dot" aria-hidden="true"></span>Sip &amp; Snack Bright, on the run!<span class="dot" aria-hidden="true"></span></p>
  </section>
</body>
</html>
```